Velmora Consulting Business

** Please add the content information from my old business card
1. I would like to see a two sided business card with both options with the 1st Option--Tallow Spire-new WHITE BACKGROUND LOGO
2 nd Option-Tallow Spire - new BLACK- Background Logo
3rd -Option a business card with my Photo on the card
Please add the new word to the card information:
EXECUTION
AS THE OWNER'S REP
WE AIM TO ACHIEVE YOUR
INFRASTRUCTURE VISION with
OUR SPECIALIZATION & EXECUTION in:

FUNDING Planning
BUSINESS Planning
INFRASTRUCTURE Planning
PROJECT Management
Since 2012
_____________________________________________________________________
I want to get spot uv raised printing. I was liking a a nice rich white linen paper stock with black writing & NOT A COLORED CARD other than a variety of white or black cards concept

```html
<!DOCTYPE html>
<html lang="en">
<head>
<meta charset="utf-8">
<title>Velmora Consulting – Business Card</title>
<link rel="stylesheet" href="https://fonts.googleapis.com/css2?family=Arimo:wght@400;700&display=swap">
<style>
  :root {
    --backdrop: #e4e3e1;
    --card: #2b2a2e;
    --edge: #d71920;
    --accent: #e0242b;
    --ink: #ffffff;
    --rule: #c9c9c9;
  }
  * { box-sizing: border-box; margin: 0; padding: 0; }
  html, body { width: 1200px; height: 801px; overflow: hidden; }
  body {
    background: var(--backdrop);
    font-family: "Arimo", Arial, sans-serif;
    color: var(--ink);
    position: relative;
  }
  .card {
    position: absolute;
    top: 246px;
    width: 540px;
    height: 309px;
    background: var(--card);
    border-bottom: 4px solid var(--edge);
    border-left: 2px solid var(--edge);
    box-shadow: 0 14px 30px rgba(0,0,0,0.25);
    overflow: hidden;
  }
  .card--front { left: 40px; }
  .card--back { left: 620px; }

  /* brand wordmark */
  .brand {
    position: absolute;
    display: flex;
    align-items: center;
    gap: 10px;
    font-weight: 700;
    color: var(--ink);
    white-space: nowrap;
    line-height: 1.1;
  }
  .brand__mark {
    width: 14px; height: 14px;
    background: var(--accent);
    flex: none;
  }
  .brand__name span { display: block; }
  .card--front .brand { left: 60px; top: 122px; font-size: 28px; max-width: 190px; }
  .card--back .brand { left: 30px; top: 222px; font-size: 30px; }
  .card--back .brand__name span { display: inline; }

  /* front: contact details */
  .divider {
    position: absolute;
    left: 270px; top: 40px;
    width: 1px; height: 230px;
    background: var(--rule);
  }
  .contact {
    position: absolute;
    left: 292px; top: 52px;
    font-size: 13px;
    line-height: 1.4;
  }
  .contact__name { color: var(--accent); font-weight: 700; font-size: 17px; }
  .contact__role { margin-bottom: 14px; }
  .contact__place { margin-bottom: 14px; }
  .contact__line { display: flex; align-items: center; gap: 8px; }
  .contact__line svg { width: 12px; height: 12px; flex: none; }

  /* back: statement */
  .statement {
    position: absolute;
    right: 26px; top: 24px;
    text-align: right;
    font-size: 13.5px;
    line-height: 1.32;
  }
  .statement .hl { color: var(--accent); font-weight: 700; }
  .statement__rule {
    height: 1px; background: var(--accent);
    width: 330px; margin: 4px 0 6px auto;
  }
  .services { list-style: none; }
  .services li { display: flex; justify-content: flex-end; align-items: center; gap: 8px; }
  .services li::after {
    content: ""; width: 7px; height: 7px; border-radius: 50%;
    background: var(--accent); flex: none;
  }
  .base-rule {
    position: absolute;
    left: 30px; right: 130px; bottom: 30px;
    height: 1px; background: var(--accent);
  }
  .since {
    position: absolute;
    right: 0; bottom: 18px;
    background: var(--accent);
    padding: 5px 16px 5px 22px;
    font-size: 15px;
    clip-path: polygon(10px 0, 100% 0, 100% 100%, 10px 100%, 0 50%);
  }
</style>
</head>
<body>

  <section class="card card--front" aria-label="Card front">
    <div class="brand"><span class="brand__mark"></span><span class="brand__name"><span>Velmora</span> <span>Consulting</span></span></div>
    <div class="divider"></div>
    <div class="contact">
      <p class="contact__name">Marisol Trevane-Okafor</p>
      <p class="contact__role">CEO / Lead Project Manager</p>
      <p class="contact__place">Northgate NT<br>Riverbend NB</p>
      <p class="contact__line">
        <svg viewBox="0 0 12 12"><path d="M3 1 L5 3.5 L4 5 Q5 7 7 8 L8.5 7 L11 9 L9.5 11 Q4 10.5 1 3 Z" fill="var(--accent)"/></svg>
        555.013.2048
      </p>
      <p class="contact__line">
        <svg viewBox="0 0 12 12"><rect x="1" y="2.5" width="10" height="7" fill="none" stroke="var(--accent)" stroke-width="1.2"/><path d="M1 2.5 L6 6.5 L11 2.5" fill="none" stroke="var(--accent)" stroke-width="1.2"/></svg>
        mari@velmora.ca
      </p>
      <p class="contact__line">
        <svg viewBox="0 0 12 12"><circle cx="6" cy="6" r="5" fill="none" stroke="var(--accent)" stroke-width="1.2"/><ellipse cx="6" cy="6" rx="2.2" ry="5" fill="none" stroke="var(--accent)" stroke-width="1"/><path d="M1 6 H11" stroke="var(--accent)" stroke-width="1"/></svg>
        www.velmora.ca
      </p>
    </div>
  </section>

  <section class="card card--back" aria-label="Card back">
    <div class="statement">
      <p>EXECUTION</p>
      <p>AS THE <span class="hl">OWNER'S REP</span></p>
      <p>WE AIM TO ACHIEVE YOUR</p>
      <p>INFRASTRUCTURE VISION with</p>
      <p>OUR SPECIALIZATION &amp; EXECUTION in:</p>
      <div class="statement__rule"></div>
      <ul class="services">
        <li>FUNDING Planning</li>
        <li>BUSINESS Planning</li>
        <li>INFRASTRUCTURE Planning</li>
        <li>PROJECT Management</li>
      </ul>
    </div>
    <div class="brand"><span class="brand__mark"></span><span class="brand__name"><span>Velmora</span> <span>Consulting</span></span></div>
    <div class="base-rule"></div>
    <div class="since">Since 2012</div>
  </section>

</body>
</html>
```